Vantiqo custom business card design

Need a authentic, innovative business card design for a new mobile app business. I am uploading a few screen images from our app for you to view. I would like app design theme to match business card design. I can also send logo images.

```html
<!DOCTYPE html>
<html lang="en">
<head>
<meta charset="utf-8">
<title>Vantiqo Business Card</title>
<link href="https://fonts.googleapis.com/css2?family=Work+Sans:wght@400;500;800&display=swap" rel="stylesheet">
<style>
  :root {
    --stage: #121212;
    --card: #1c1c1c;
    --card-edge: #262626;
    --emboss: #2e2e2e;
    --emboss-shade: #0c0c0c;
    --silver: #e4e4e4;
    --silver-soft: #a9a9a9;
    --rule: #555555;
  }
  * { margin: 0; padding: 0; box-sizing: border-box; }
  html, body {
    width: 1200px; height: 900px; overflow: hidden;
    background: var(--stage);
    font-family: "Work Sans", Arial, sans-serif;
  }
  .stage {
    position: relative; width: 1200px; height: 900px;
    background: radial-gradient(ellipse at 50% 45%, #222 0%, var(--stage) 70%);
  }
  .card {
    position: absolute; left: 290px; width: 620px; height: 354px;
    background: linear-gradient(135deg, var(--card-edge) 0%, var(--card) 55%, #181818 100%);
    box-shadow: 0 18px 40px rgba(0,0,0,.6);
  }
  .card--front { top: 60px; }
  .card--back { top: 486px; }

  .brand {
    position: absolute; inset: 0;
    display: flex; flex-direction: column; align-items: center; justify-content: center;
    gap: 18px;
  }
  .brand__dot {
    width: 92px; height: 92px; border-radius: 50%;
    background: linear-gradient(135deg, #f2f2f2, #7a7a7a);
  }
  .brand__name {
    font-weight: 800; font-size: 40px; letter-spacing: 0.5px;
    color: var(--silver);
  }

  .details {
    position: absolute; inset: 0;
    display: flex; align-items: center; justify-content: center;
    padding-left: 30px;
  }
  .identity {
    text-align: right; padding-right: 30px;
    color: var(--emboss);
    text-shadow: -1px -1px 0 var(--emboss-shade), 1px 1px 0 #3a3a3a;
  }
  .identity__name { font-size: 24px; font-weight: 500; letter-spacing: 1px; text-transform: uppercase; }
  .identity__role { font-size: 17px; margin-top: 4px; }
  .identity__addr { font-size: 17px; line-height: 1.4; margin-top: 4px; }
  .divider { width: 1px; height: 96px; background: var(--rule); }
  .contacts { list-style: none; padding-left: 36px; color: var(--silver); }
  .contacts li {
    display: flex; align-items: center; gap: 14px;
    font-size: 18px; letter-spacing: 1px; line-height: 29px;
  }
  .contacts svg { width: 14px; height: 14px; stroke: var(--silver-soft); fill: none; stroke-width: 1.4; flex: none; }
</style>
</head>
<body>
<main class="stage">
  <section class="card card--front" aria-label="Card front">
    <div class="brand">
      <span class="brand__dot"></span>
      <span class="brand__name">Vantiqo</span>
    </div>
  </section>

  <section class="card card--back" aria-label="Card back">
    <div class="details">
      <div class="identity">
        <p class="identity__name">Daniel Reyes</p>
        <p class="identity__role">Director</p>
        <p class="identity__addr">1480 Harbor Lane<br>Coral Bay, FL 32090</p>
      </div>
      <span class="divider"></span>
      <ul class="contacts">
        <li><svg viewBox="0 0 14 14"><rect x="3.5" y="1" width="7" height="12" rx="1.2"/><line x1="6" y1="11" x2="8" y2="11"/></svg>(555) 214-7730</li>
        <li><svg viewBox="0 0 14 14"><path d="M3 1.5l2.2 2.5-1.2 1.5c.8 1.8 2.2 3.2 4 4l1.5-1.2 2.5 2.2-1.5 2c-5-.5-9-4.5-9.5-9.5z"/></svg>(555) 386-0912</li>
        <li><svg viewBox="0 0 14 14"><rect x="1" y="3" width="12" height="8.5" rx="1"/><path d="M1 3.5l6 4.5 6-4.5"/></svg>info@Vantiqo.com</li>
        <li><svg viewBox="0 0 14 14"><circle cx="7" cy="7" r="5.8"/><ellipse cx="7" cy="7" rx="2.6" ry="5.8"/><line x1="1.2" y1="7" x2="12.8" y2="7"/></svg>www.Vantiqo.com</li>
      </ul>
    </div>
  </section>
</main>
</body>
</html>
```